RTavenor Business Cards & Letterhead

I have a logo but need a design for some new business cards. We are a Design-Build Firm that specializes in the design and construction of commercial projects.
the cards need to be professional. no cartoon stuff.
i would like to have the cards in AI format so I can update the card as needed. Logo is provided.
Our Address is: 4187 Marlowe Ct. Apex, North Carolina 27614

```html
<!DOCTYPE html>
<html lang="en">
<head>
<meta charset="utf-8">
<title>RTavenor Business Card</title>
<link rel="stylesheet" href="https://fonts.googleapis.com/css2?family=Open+Sans:wght@400;600;700;800&display=swap">
<style>
  :root {
    --stage: #232323;
    --card-black: #0d0d0f;
    --card-face: #1f1f23;
    --brand-blue: #1479bf;
    --brand-blue-deep: #0d5a95;
    --wordmark-grey: #8e8e92;
    --text-light: #f2f2f2;
    --rule: #bdbdbd;
  }
  * { box-sizing: border-box; margin: 0; padding: 0; }
  html, body {
    width: 1200px; height: 780px; overflow: hidden;
    background: var(--stage);
    font-family: "Open Sans", Arial, sans-serif;
  }
  .canvas {
    position: relative; width: 1200px; height: 780px;
    display: flex; align-items: center; justify-content: center; gap: 48px;
  }
  .card {
    position: relative; width: 540px; height: 309px;
    border-radius: 4px; overflow: hidden;
    box-shadow: 0 18px 40px rgba(0,0,0,.55);
  }
  /* Back */
  .card-back { background: var(--card-black); }
  .card-back .pattern {
    position: absolute; inset: 0;
    background:
      radial-gradient(ellipse 70% 60% at 92% 0%, rgba(210,210,215,.55), rgba(120,120,125,.18) 45%, transparent 70%),
      linear-gradient(160deg, #1a1a1d 0%, #08080a 60%, #050506 100%);
  }
  .card-back .wordmark {
    position: absolute; right: 44px; bottom: 104px;
    display: flex; align-items: center; gap: 10px;
  }
  .wordmark .mark-square {
    width: 22px; height: 22px; background: var(--brand-blue);
  }
  .wordmark .mark-name {
    font-weight: 800; font-size: 40px; letter-spacing: 1px;
    color: var(--wordmark-grey); line-height: 1;
  }
  /* Front */
  .card-front { background: var(--card-face); }
  .card-front .brand {
    position: absolute; left: 0; top: 0; width: 226px; height: 100%;
    display: flex; flex-direction: column; align-items: center; justify-content: center; gap: 14px;
  }
  .brand .brand-square {
    width: 88px; height: 88px; border-radius: 8px;
    background: linear-gradient(135deg, var(--brand-blue), var(--brand-blue-deep));
  }
  .brand .brand-name {
    font-weight: 700; font-size: 26px; color: var(--brand-blue);
  }
  .card-front .divider {
    position: absolute; left: 234px; top: 62px; width: 1px; height: 190px;
    background: var(--rule);
  }
  .card-front .details {
    position: absolute; left: 262px; top: 58px; right: 16px;
    color: var(--text-light);
  }
  .details .person-name {
    font-weight: 800; font-size: 25px; color: var(--brand-blue);
    letter-spacing: .5px; line-height: 1.05; white-space: nowrap;
  }
  .details .person-title {
    font-weight: 700; font-size: 14px; margin-top: 3px;
  }
  .details .address {
    font-size: 13.5px; line-height: 1.35; margin-top: 18px; padding-left: 20px;
  }
  .details .contacts {
    list-style: none; margin-top: 18px; padding-left: 20px;
    font-size: 13.5px; line-height: 1.45;
  }
  .contacts li { display: flex; align-items: center; gap: 8px; }
  .contacts svg { width: 12px; height: 12px; flex: none; }
</style>
</head>
<body>
<main class="canvas">
  <section class="card card-back" aria-label="Business card back">
    <div class="pattern" role="img" aria-label="Repeating gloss-black monogram pattern with a silver sheen in the top corner"></div>
    <div class="wordmark">
      <span class="mark-square"></span>
      <span class="mark-name">RTAVENOR</span>
    </div>
  </section>

  <section class="card card-front" aria-label="Business card front">
    <div class="brand">
      <span class="brand-square"></span>
      <span class="brand-name">RTavenor</span>
    </div>
    <div class="divider"></div>
    <div class="details">
      <p class="person-name">REID TAVENOR</p>
      <p class="person-title">Founder/President</p>
      <p class="address">4187 Marlowe Ct. Apex,<br>North Carolina 27614</p>
      <ul class="contacts">
        <li>
          <svg viewBox="0 0 12 12" aria-hidden="true"><path fill="#1479bf" d="M2.4 0.8l2 2-1 1.2c.6 1.6 2 3 3.6 3.6l1.2-1 2 2-1.4 1.6C5 10 2 7 1 2.2z"/></svg>
          (919) 555-0148
        </li>
        <li>
          <svg viewBox="0 0 12 12" aria-hidden="true"><circle cx="6" cy="6" r="5" fill="none" stroke="#1479bf" stroke-width="1.4"/><ellipse cx="6" cy="6" rx="2" ry="5" fill="none" stroke="#1479bf" stroke-width="1"/><path d="M1 6h10" stroke="#1479bf" stroke-width="1"/></svg>
          www.rtavenor.com
        </li>
        <li>
          <svg viewBox="0 0 12 12" aria-hidden="true"><rect x="0.7" y="2.2" width="10.6" height="7.6" rx="1" fill="none" stroke="#1479bf" stroke-width="1.3"/><path d="M1 2.8l5 3.8 5-3.8" fill="none" stroke="#1479bf" stroke-width="1.2"/></svg>
          RMT@RTavenor.com
        </li>
      </ul>
    </div>
  </section>
</main>
</body>
</html>
```